BrimLO (Beer/Wine candles) Edgy Candle with a Cause

Help us to help others. BrimLo is a beautifully scented natural soy candle made using repurposed beer/ wine bottles while at the same time donating a portion of our profits to youth alcohol education programs. (1. Brim = Repurposed beer/wine bottle, 2.) BrimLo = (anti) drunk/alcohol 3.) LO = education/prevention programs.)
We're looking for a design that is cool and bold yet elegant and appeals to women (90% of our customers.) No traditional beer label designs please.

The "BrimLO" logo should appear prominently in the design with the scent name (in a different font) "on top." (See the "Velvet Brimmed" poster attached.

Examples of actual scents: Amber Drift, Glowing Paloma, Fizzing Mock-ree. (None of the fragrances smell like beer/alcohol or wine.)

Also the LO in BrimeLO should stand out in some way.

The emphasis should not be on the recycling aspect, so no obvious recycling symbols.

We are open to different interpretations and have attached varying examples that we like.
Note: a "blackboard/chalkboard" label is an idea since this deals with education.

Note: files & fonts used in the final design should be editable so that we can add other scent names as needed.

Target Market(s)

Candle buyers, specifically women between the ages of 16-45

Requirements
Must have
• 1.)Free fonts or license fonts under $20.00 2.) fonts modified to look unique/original. 3.) Editable Scent name 4.) Burning instructions 5.) Warning Info
• Burning Instructions: Trim wick to 1/4" before each lighting. Keep free from foreign materials including wick trimmings. For an even burn, burn for at least 1 hour but not more than 4 hours at a time. Discontinue use when 1/4" of wax remains. Discard or recycle after use.
• Warning: Burn candle within sight. Keep out of reach of children and pets. Keep away from things that catch fire. Use with caution.
Nice to have
• Colored Scent Names
Should not have
• recycle symbols

```html
<!DOCTYPE html>
<html lang="en">
<head>
<meta charset="utf-8">
<title>BrimLO – Amber Drift Candle Label</title>
<link rel="stylesheet" href="https://fonts.googleapis.com/css2?family=Gochi+Hand&family=Mrs+Saint+Delafield&display=swap">
<style>
  :root {
    --board: #0f0f0f;
    --board-edge: #050505;
    --chalk: #b9b9b9;
    --chalk-soft: #9a9a9a;
    --frame: #d6d6d6;
    --mark-grey: #8e8e8e;
    --scent-tan: #c79a6a;
    --wordmark: #ffffff;
    --accent-green: #7ac143;
  }
  html, body {
    margin: 0;
    padding: 0;
    width: 1200px;
    height: 800px;
    overflow: hidden;
    background: var(--board-edge);
  }
  .label {
    position: relative;
    width: 1200px;
    height: 800px;
    background: radial-gradient(ellipse at 50% 40%, #1c1c1c 0%, var(--board) 55%, var(--board-edge) 100%);
    font-family: "Gochi Hand", cursive;
    color: var(--chalk);
    overflow: hidden;
  }
  .frame {
    position: absolute;
    left: 40px; top: 42px;
    width: 1114px; height: 710px;
    border: 3px solid var(--frame);
    border-radius: 8px;
  }
  .chalk-block {
    position: absolute;
    margin: 0;
    text-align: right;
    white-space: nowrap;
  }
  .about {
    right: 832px; top: 70px;
    font-size: 26px;
    line-height: 29px;
    transform: rotate(-5deg);
    transform-origin: right top;
  }
  .instructions-title {
    position: absolute;
    left: 902px; top: 72px;
    padding: 2px 10px;
    border: 2px solid var(--chalk-soft);
    border-left-style: dashed;
    font-size: 24px;
    transform: rotate(4deg);
  }
  .instructions {
    right: 64px; top: 128px;
    font-size: 24px;
    line-height: 25px;
    transform: rotate(5deg);
    transform-origin: right top;
  }
  .warning-title {
    position: absolute;
    left: 892px; top: 524px;
    width: 156px; height: 56px;
    border: 2px solid var(--chalk-soft);
    border-radius: 50%;
    box-sizing: border-box;
    text-align: center;
    line-height: 52px;
    font-size: 26px;
    transform: rotate(-8deg);
  }
  .warning {
    right: 82px; top: 596px;
    font-size: 27px;
    line-height: 29px;
    transform: rotate(-4deg);
    transform-origin: right top;
  }
  .meaning {
    right: 818px; top: 566px;
    font-size: 23px;
    line-height: 26px;
    transform: rotate(4deg);
    transform-origin: right top;
  }
  .brand-mark {
    position: absolute;
    left: 0; right: 0; top: 106px;
    margin: 0;
    text-align: center;
    font-size: 132px;
    line-height: 1;
    color: var(--mark-grey);
  }
  .scent-name {
    position: absolute;
    left: 0; right: 0; top: 364px;
    margin: 0;
    text-align: center;
    font-family: "Mrs Saint Delafield", cursive;
    font-size: 76px;
    line-height: 1;
    color: var(--scent-tan);
  }
  .wordmark {
    position: absolute;
    left: 0; right: 0; top: 430px;
    margin: 0;
    text-align: center;
    font-family: "Gochi Hand", cursive;
    font-weight: 400;
    font-size: 136px;
    line-height: 1;
    color: var(--wordmark);
  }
  .strokes {
    position: absolute;
    left: 0; top: 0;
    width: 1200px; height: 800px;
    pointer-events: none;
  }
</style>
</head>
<body>
<main class="label">
  <div class="frame"></div>

  <p class="chalk-block about">BrimLo is a beautifully<br>scented natural soy<br>candle made using<br>repurposed beer/ wine<br>bottles while at the<br>same time donating a<br>portion of our profits to<br>youth alcohol education<br>programs.</p>

  <p class="brand-mark">BrimLO</p>

  <div class="instructions-title">Burning Instructions:</div>
  <p class="chalk-block instructions">Trim wick to 1/4" before<br>each lighting. Keep free<br>from foreign materials<br>including wick trimmings. For<br>an even burn, burn for at<br>least 1 hour but not more<br>than 4 hours at a time.<br>Discontinue use when 1/4"<br>of wax remains. Discard or<br>recycle after use.</p>

  <p class="scent-name">Amber Drift</p>
  <h1 class="wordmark">BrimLO</h1>

  <svg class="strokes" viewBox="0 0 1200 800" aria-hidden="true">
    <path d="M176 342 C 112 400, 116 510, 170 560" fill="none" stroke="#8a8a8a" stroke-width="2.5" stroke-linecap="round"/>
    <path d="M162 558 L172 562 L170 551" fill="none" stroke="#8a8a8a" stroke-width="2" stroke-linecap="round"/>
    <path d="M426 598 C 580 590, 740 582, 870 574" fill="none" stroke="var(--accent-green)" stroke-width="7" stroke-linecap="round"/>
    <path d="M432 606 C 560 598, 700 590, 858 582" fill="none" stroke="var(--accent-green)" stroke-width="3" stroke-linecap="round" opacity="0.7"/>
    <path d="M436 640 C 520 632, 610 624, 690 618" fill="none" stroke="var(--accent-green)" stroke-width="6" stroke-linecap="round"/>
  </svg>

  <p class="chalk-block meaning">1. Brim = Repurposed<br>beer/wine bottle,<br>2.) BrimLo = (anti)<br>drunk/alcohol<br>3.) LO = education/prevention<br>programs.</p>

  <div class="warning-title">Warning:</div>
  <p class="chalk-block warning">burn candle within sight.<br>Keep out of reach of children<br>and pets. Keep away from<br>things that catch fire.<br>Use with caution.</p>
</main>
</body>
</html>
```